We need UI/UX design for a public, informational website for The Copper Lantern.
The pages, structure, and content scope are already defined. Designers are required to work only on the UI/UX layout of these existing pages, focusing on clarity, hierarchy, spacing, and usability. Do not add, remove, rename, or reinterpret pages or content.
The website is strictly informational only. It must not include accounts, onboarding, payments, custody, escrow administration, marketplaces, dashboards, or any transactional functionality.
Scope of work
Apply UI/UX design to the predefined website pages
Design layout for text, images, notices, and sections
Ensure consistent components and layout patterns across page types
Optimize layouts for long form, compliance focused content
Content writing, page creation, and branding changes are out of scope.
Structure reference
The complete page list, hierarchy, and content definitions are provided in the technical documentation and must be treated as the primary source of truth.
A Figma link is provided only as a light visual reference for page existence and structure:
https://meadow-knot-48203956.plumsite.example/
Designers must rely on the documentation for in depth and authoritative reference.
Brand guidelines
The Copper Lantern has existing brand guidelines and official logos, including light and dark versions. These assets will be provided and must be followed exactly. Designers must not redesign, alter, or reinterpret the brand identity.
Look and feel direction
The desired visual direction is inspired by:
https://ledgerwaltz.example/
This reference is provided only to indicate:
Institutional and enterprise tone
Clean, modern typography
Strong hierarchy and generous whitespace
Editorial, content first layouts
Do not copy branding, layouts, components, or assets from the reference site.
Hero section direction
The hero section should follow a similar structural approach to the hero used on https://ledgerwaltz.example/
, meaning:
Strong editorial framing
Clear headline hierarchy
Calm, institutional first impression
However, the background video must be Abu Dhabi focused, not generic or global. The video should visually reflect:
Abu Dhabi skyline or architectural language
Institutional, sovereign, long term infrastructure tone
Clean, slow, cinematic motion
No promotional, marketing, or lifestyle visuals
The hero must remain informational, restrained, and credible. No hype. No calls to invest. No implied participation.
Constraints
One global primary CTA only: “Continue to Halvemark” (external)
All other interactions must be informational
No visuals or language implying offers, investment, eligibility, or participation
Clear separation between informational content and any external operational platforms
Deliverables
High fidelity UI/UX designs created in Figma, covering:
Desktop layouts
Tablet layouts where relevant
Mobile layouts
Complete Figma file(s) including:
All designed pages defined in the technical documentation
A reusable component library (headers, footers, cards, notice panels, forms, CTAs, typography styles, spacing system)
Clearly defined layout grids, spacing rules, and text styles
Proper use of components and variants, not detached frames
Designs prepared for developer handoff, including:
Clear layer naming and structure
Auto layout where appropriate
Consistent use of styles and components
Responsive behavior demonstrated within Figma
Notes or annotations only where necessary for clarity
No prototypes, interactions, or motion design beyond basic layout states, unless explicitly requested. The focus is static UI/UX clarity, not animation.
A detailed technical specification document and official brand assets will be provided.
Any designs delivered outside Figma, that alter structure or content, or that ignore the defined constraints, boundaries, or tone will be rejected.

```html
<!DOCTYPE html>
<html lang="en">
<head>
<meta charset="utf-8">
<title>The Copper Lantern</title>
<link href="https://fonts.googleapis.com/css2?family=Poppins:wght@300;400;500;600&display=swap" rel="stylesheet">
<style>
:root{
  --ink:#111522;
  --muted:#3d4250;
  --line:#e3e6ee;
  --accent-a:#3f8cff;
  --accent-b:#9b5cff;
  --cyan:#2ec5e8;
  --navy:#0b1428;
  --navy-line:#263250;
  --notice:#eceef1;
  --white:#ffffff;
}
*{box-sizing:border-box;margin:0;padding:0}
html,body{width:1200px;height:4528px;overflow:hidden}
body{font-family:"Poppins",Arial,sans-serif;color:var(--ink);background:var(--white);position:relative}
.grad-btn{display:inline-block;background:linear-gradient(90deg,var(--accent-a),var(--accent-b));color:var(--white);font-size:15px;font-weight:500;padding:12px 26px;border-radius:6px;text-decoration:none}

/* header */
.site-header{position:absolute;top:0;left:0;width:1200px;height:80px;display:flex;align-items:center;padding:0 60px;background:var(--white)}
.brand{display:flex;align-items:center;gap:10px;font-size:18px;font-weight:500;color:var(--ink)}
.brand-dot{width:26px;height:26px;border-radius:50%;border:2px solid var(--ink)}
.main-nav{display:flex;gap:30px;margin-left:auto;margin-right:40px;font-size:15px}
.main-nav span{color:var(--ink)}
.site-header .grad-btn{font-size:14px;padding:11px 22px}

/* hero */
.hero{position:absolute;top:80px;left:0;width:1200px;height:660px;background:linear-gradient(180deg,#4e82b8 0%,#8db6d8 35%,#b9cfd8 58%,#37a5b9 72%,#d8cdb5 88%,#c9b89a 100%)}
.hero-copy{position:absolute;left:636px;top:480px;color:var(--white)}
.hero-copy h1{font-size:50px;font-weight:400;margin-bottom:22px;line-height:1.2}

/* intro */
.intro{position:absolute;top:740px;left:0;width:1200px;height:440px}
.intro-badge{position:absolute;left:240px;top:40px;width:130px;height:120px;border-radius:6px;background:linear-gradient(135deg,var(--accent-a),var(--accent-b));color:var(--white);display:flex;flex-direction:column;align-items:center;justify-content:center}
.intro-badge strong{font-size:40px;font-weight:500;line-height:1}
.intro-badge span{font-size:12px;margin-top:6px}
.intro-photo{position:absolute;left:110px;top:120px;width:380px;height:220px;background:linear-gradient(135deg,#f5f6f8,#c9ccd3 60%,#8e939c)}
.intro-orbit{position:absolute;left:0;top:0}
.intro-text{position:absolute;left:780px;top:50px;width:360px;font-size:14px;line-height:1.6;color:var(--muted)}
.intro-text p{margin-bottom:20px}

/* feature rows */
.feature{position:absolute;left:0;width:1200px}
.feature h2{font-size:34px;font-weight:500;line-height:1.25;margin-bottom:24px;color:var(--ink)}
.feature p{font-size:14px;line-height:1.65;color:var(--muted);margin-bottom:18px}
.feature-copy{position:absolute;width:430px}
.feature-media{position:absolute;width:310px;height:340px}

/* ecosystem */
.ecosystem{position:absolute;top:2200px;left:0;width:1200px;text-align:center}
.ecosystem h2{font-size:34px;font-weight:500;margin-bottom:20px}
.ecosystem .lead{font-size:14px;color:var(--muted);width:520px;margin:0 auto;line-height:1.6}
.steps{position:relative;height:260px;margin-top:30px}
.step{position:absolute;top:60px;width:300px}
.step-num{width:40px;height:40px;border-radius:50%;margin:0 auto 12px;background:linear-gradient(135deg,var(--accent-a),var(--accent-b));color:var(--white);display:flex;align-items:center;justify-content:center;font-size:15px}
.step h3{font-size:18px;font-weight:500;margin-bottom:10px}
.step p{font-size:13px;line-height:1.6;color:var(--muted);width:240px;margin:0 auto}
.ecosystem .foot{font-size:14px;color:var(--muted);width:720px;margin:0 auto;line-height:1.6}

/* contact */
.contact{position:absolute;top:3640px;left:0;width:1200px;text-align:center}
.contact h2{font-size:34px;font-weight:500;margin-bottom:20px}
.contact p{font-size:14px;color:var(--muted);line-height:1.6;width:620px;margin:0 auto 16px}
.notice{position:absolute;top:3870px;left:260px;width:680px;height:190px;background:var(--notice);padding:40px 46px}
.notice h3{font-size:24px;font-weight:500;margin-bottom:14px}
.notice p{font-size:14px;color:var(--muted);line-height:1.6;width:560px}

/* footer */
.site-footer{position:absolute;top:4120px;left:0;width:1200px;height:408px;background:var(--navy);color:var(--white)}
.footer-brand{position:absolute;left:130px;top:46px}
.footer-brand .brand{color:var(--white)}
.footer-brand .brand-dot{border-color:var(--white)}
.footer-brand p{font-size:15px;line-height:1.5;margin-top:40px;width:250px}
.footer-col{position:absolute;top:46px;font-size:14px;line-height:1.75}
.footer-col h4{font-size:14px;font-weight:500;color:var(--accent-a);margin-bottom:6px}
.footer-bottom{position:absolute;left:0;top:300px;width:1200px;border-top:1px solid var(--navy-line);padding-top:22px;text-align:center;font-size:13px;line-height:2}
</style>
</head>
<body>

<header class="site-header">
  <div class="brand"><span class="brand-dot"></span>The Copper Lantern</div>
  <nav class="main-nav">
    <span>Framework ▾</span><span>Projects</span><span>Halvemark</span><span>Insights</span><span>Company ▾</span><span>Contact</span>
  </nav>
  <a class="grad-btn" href="#">Continue to Halvemark</a>
</header>

<section class="hero" role="img" aria-label="Waterfront city skyline of tall glass towers above a calm turquoise bay and sandy beach">
  <div class="hero-copy">
    <h1>The Copper Lantern</h1>
    <a class="grad-btn" href="#">Continue to Halvemark</a>
  </div>
</section>

<section class="intro">
  <svg class="intro-orbit" width="560" height="440" aria-hidden="true">
    <path d="M60 200 Q 120 360 360 300" fill="none" stroke="#3f8cff" stroke-width="2"/>
    <circle cx="360" cy="300" r="7" fill="#3f8cff"/>
  </svg>
  <div class="intro-photo" role="img" aria-label="Upward view of a modern glass and steel tower facade"></div>
  <div class="intro-badge"><strong>12+</strong><span>Years Experience</span></div>
  <div class="intro-text">
    <p>The Copper Lantern is a governance and project origination group focused on defining structural standards and oversight principles for complex initiatives. These initiatives may involve multiple parties, staged execution, and long-term accountability.</p>
    <p>The purpose of this site is to publish those standards and explain how responsibilities are deliberately separated across governance, operations, and project-level execution.</p>
    <p>This website is strictly informational.</p>
    <p>It does not provide onboarding, account access, eligibility criteria, custody of funds, escrow administration, or transaction execution. Where operational workflows exist, they are delivered through a separate operating platform governed by its own terms, policies, and controls.</p>
  </div>
</section>

<section class="feature" style="top:1300px">
  <div class="feature-copy" style="left:130px;top:40px">
    <h2>Governance and Project Origination</h2>
    <p>Governance refers to the standards that determine how initiatives are structured and how oversight is defined. Origination refers to the initial design of an initiative—establishing role separation, reporting expectations, and clear boundaries before execution begins.</p>
    <p>The Copper Lantern operates exclusively at this governance and origination layer. It does not manage day-to-day operations or project execution.</p>
  </div>
  <div class="feature-media" style="left:652px;top:0;height:340px;background:linear-gradient(135deg,#1a1d24,#3a3f4a 55%,#101216)" role="img" aria-label="Hand ticking boxes on a checklist"></div>
</section>

<section class="feature" style="top:1720px">
  <div class="feature-media" style="left:140px;top:0;height:240px;background:linear-gradient(135deg,#f4f4f6,#d3d5da 50%,#9ea2aa)" role="img" aria-label="Abstract white curved architectural ribbons"></div>
  <div class="feature-copy" style="left:660px;top:50px;width:410px">
    <h2>Clear Role Separation</h2>
    <p>The ecosystem is designed around clear separation of responsibilities. Governance activities belong at the framework layer. Operational workflows, where available, belong on a separate operating platform designed for process execution and recordkeeping. Assets and project execution, where applicable, belong at the project level through ring-fenced structures created for specific initiatives. This separation is intended to reduce ambiguity and help stakeholders understand who is responsible for what.</p>
  </div>
</section>

<section class="ecosystem">
  <h2>How the Ecosystem Works</h2>
  <p class="lead">At a high level, the ecosystem is organised into three distinct layers, each with a clearly defined scope of responsibility.</p>
  <div class="steps">
    <svg style="position:absolute;left:0;top:0" width="1200" height="260" aria-hidden="true">
      <g fill="none" stroke="#2ec5e8" stroke-width="2">
        <path d="M130 130 A130 130 0 0 1 250 50"/>
        <path d="M470 130 A130 130 0 0 1 590 50"/>
        <path d="M810 130 A130 130 0 0 1 930 50"/>
      </g>
    </svg>
    <div class="step" style="left:100px"><div class="step-num">1</div><h3>Governance</h3><p>defines standards, explains role boundaries, and publishes framework information.</p></div>
    <div class="step" style="left:440px"><div class="step-num">2</div><h3>Operations</h3><p>manages workflow processes such as documentation steps and record-bound audit events through a separate platform.</p></div>
    <div class="step" style="left:780px"><div class="step-num">3</div><h3>Project Execution</h3><p>occurs at the project level through dedicated structures that hold responsibilities and assets where applicable.</p></div>
  </div>
  <p class="foot">This website focuses on the governance layer and provides links to learn about structural concepts such as role separation, escrow and milestone framing, and recordkeeping terminology.</p>
</section>

<section class="feature" style="top:2800px">
  <div class="feature-copy" style="left:130px;top:50px">
    <h2>Independent Escrow and Milestone Oversight</h2>
    <p>Some initiatives use independent escrow arrangements to coordinate staged releases linked to milestone completion. Escrow can support execution discipline by requiring defined evidence before releases occur. Escrow does not guarantee outcomes, timelines, or success, and it is not administered by this website operator. This site describes the concept for clarity and transparency.</p>
  </div>
  <div class="feature-media" style="left:652px;top:0;height:340px;background:linear-gradient(135deg,#1b1b1f,#4a1414 55%,#c9302c)" role="img" aria-label="Checked boxes on a form beside a red pencil"></div>
</section>

<section class="feature" style="top:3200px">
  <div class="feature-media" style="left:140px;top:0;height:320px;background:radial-gradient(circle at 50% 50%,#8a3fd1 0%,#3a1f6a 35%,#0c0a18 75%)" role="img" aria-label="Glowing neon rings on a dark background"></div>
  <div class="feature-copy" style="left:660px;top:70px;width:400px">
    <h2>Where Operational Workflows Happen</h2>
    <p>Operational workflows, including any onboarding or workflow participation where permitted, occur on a separate operating platform under separate terms and policies. If you need operational access, use the Halvemark page on this site to navigate externally. This website does not host those workflows.</p>
  </div>
</section>

<section class="contact">
  <h2>Contact and Inquiries</h2>
  <p>If you have questions regarding governance framework concepts, role boundaries, or information published on this website, you may contact the team through the Contact page.</p>
  <p>Do not submit sensitive personal data through public forms.</p>
</section>

<aside class="notice">
  <h3>Informational Notice</h3>
  <p>This website is provided for general informational purposes only. Nothing on this site is an offer, solicitation, or professional advice.</p>
</aside>

<footer class="site-footer">
  <div class="footer-brand">
    <div class="brand"><span class="brand-dot"></span>The Copper Lantern</div>
    <p>A governance framework for structured project oversight and risk management.</p>
  </div>
  <div class="footer-col" style="left:560px">
    <h4>Framework</h4>
    <div>Role Boundaries</div><div>SPV Structure</div><div>Escrow Model</div><div>Records and Registers</div><div>Risk and Boundaries</div>
  </div>
  <div class="footer-col" style="left:760px">
    <h4>Company</h4>
    <div>About</div><div>Leadership</div><div>Governance</div><div>Press</div><div>Careers</div><div>Contact</div>
  </div>
  <div class="footer-col" style="left:960px">
    <h4>Legal</h4>
    <div>Terms of Use</div><div>Privacy Policy</div><div>Cookie Policy</div><div>Disclaimer and Risk Notices</div><div>Acceptable Use</div><div>Accessibility</div>
  </div>
  <div class="footer-bottom">
    <div>© 2026 The Copper Lantern. All rights reserved.</div>
    <div>This website provides informational content only. The Copper Lantern does not provide investment advice, execute projects, or facilitate transactions.</div>
    <div>All operational activities are conducted through Halvemark, a separate platform.</div>
  </div>
</footer>

</body>
</html>
```